IT Company requires new Business Card design.

Over the years we have had a few different business card designs. We are now due for new cards across the board for all staff. We felt this would be a good time to start fresh with a new design. Our traditional card simply had our details on the front, and a list of services on the back. We don't particularly need the list of services, we have had cards where the only thing on the rear of the card was our logo.
Feel free to be creative, we would like our tag line "Complete IT Management" to appear at some point, doesn't necessarily have to be with the logo.
I have attached samples and drafts of various previous cards we have used over the years.

```html
<!DOCTYPE html>
<html lang="en">
<head>
<meta charset="utf-8">
<title>Harbor Systems – Business Cards</title>
<link href="https://fonts.googleapis.com/css2?family=Open+Sans:wght@400;600;700;800&display=swap" rel="stylesheet">
<style>
  :root {
    --bg: #e9e8ee;
    --card: #ffffff;
    --slate: #5f7382;
    --charcoal: #474749;
    --ink: #3d3d3f;
    --light: #ffffff;
    --divider: #8a8a8e;
  }
  * { box-sizing: border-box; margin: 0; padding: 0; }
  html, body { width: 1200px; height: 987px; overflow: hidden; }
  body {
    background: var(--bg);
    font-family: "Open Sans", Arial, sans-serif;
    position: relative;
  }
  .card {
    position: absolute;
    width: 620px;
    height: 378px;
    background: var(--card);
    border-radius: 26px;
    overflow: hidden;
    box-shadow: 0 10px 30px rgba(60, 60, 80, 0.18);
  }
  /* Back of card */
  .card-back { left: 520px; top: 60px; }
  .card-back .wordmark {
    position: absolute;
    left: 0; right: 0; top: 120px;
    display: flex; align-items: center; justify-content: center; gap: 18px;
    color: var(--slate);
    font-weight: 800;
    font-size: 46px;
    letter-spacing: 1px;
    text-transform: uppercase;
  }
  .mark-square { width: 40px; height: 40px; background: var(--slate); flex: none; }
  .card-back .web {
    position: absolute; left: 0; right: 0; bottom: 50px;
    text-align: center;
    color: var(--ink);
    font-size: 20px;
    letter-spacing: 2px;
  }
  /* Front of card */
  .card-front { left: 60px; top: 520px; }
  .card-front .brand {
    position: absolute; left: 0; right: 0; top: 0; height: 150px;
    display: flex; align-items: center; justify-content: center; gap: 16px;
    color: var(--slate);
    font-weight: 800;
    font-size: 40px;
    letter-spacing: 1px;
    text-transform: uppercase;
  }
  .card-front .brand .mark-square { width: 34px; height: 34px; }
  .contact-band {
    position: absolute; left: 0; right: 0; top: 150px; height: 178px;
    background: var(--charcoal);
    color: var(--light);
    display: flex; align-items: center; justify-content: center;
  }
  .person { text-align: right; padding-right: 22px; }
  .person .name { font-weight: 700; font-size: 22px; }
  .person .role { font-size: 17px; margin-top: 2px; }
  .person .mobile { font-size: 17px; margin-top: 8px; display: flex; justify-content: flex-end; align-items: center; gap: 8px; }
  .divider { width: 1px; height: 120px; background: var(--divider); }
  .details { list-style: none; padding-left: 22px; font-size: 17px; }
  .details li { display: flex; align-items: center; gap: 10px; line-height: 29px; }
  .icon { width: 16px; height: 16px; flex: none; fill: var(--light); }
  .tagline-band {
    position: absolute; left: 0; right: 0; bottom: 0; height: 50px;
    background: var(--slate);
    color: var(--light);
    display: flex; align-items: center; justify-content: center;
    font-size: 17px;
    letter-spacing: 5px;
    text-transform: uppercase;
  }
</style>
</head>
<body>

<section class="card card-back" aria-label="Card back">
  <div class="wordmark"><span class="mark-square"></span>Harbor Systems</div>
  <p class="web">www.harborsystems.com.au</p>
</section>

<section class="card card-front" aria-label="Card front">
  <div class="brand"><span class="mark-square"></span>Harbor Systems</div>

  <div class="contact-band">
    <div class="person">
      <p class="name">Daniel Reeve</p>
      <p class="role">Operation Manager</p>
      <p class="mobile">
        <svg class="icon" viewBox="0 0 16 16" aria-hidden="true"><rect x="4" y="0.5" width="8" height="15" rx="1.5"/><rect x="5.5" y="2.5" width="5" height="6" fill="#474749"/></svg>
        0412 908 476
      </p>
    </div>
    <div class="divider"></div>
    <ul class="details">
      <li>
        <svg class="icon" viewBox="0 0 16 16" aria-hidden="true"><path d="M3.5 1l3 3-1.8 1.8c.9 2 2.5 3.6 4.5 4.5L11 8.5l3 3-2 2.5C6.5 13.5 2.5 9.5 1 3.5z"/></svg>
        08 9552 6140
      </li>
      <li>
        <svg class="icon" viewBox="0 0 16 16" aria-hidden="true"><rect x="4" y="1" width="8" height="4"/><rect x="1" y="5.5" width="14" height="6" rx="1"/><rect x="4" y="10" width="8" height="5" fill="#ffffff" stroke="#474749"/></svg>
        08 9552 6140
      </li>
      <li>
        <svg class="icon" viewBox="0 0 16 16" aria-hidden="true"><rect x="1" y="3" width="14" height="10" rx="1"/><path d="M1.5 3.5L8 9l6.5-5.5" stroke="#474749" stroke-width="1.4" fill="none"/></svg>
        daniel@harborsystems.com.au
      </li>
      <li>
        <svg class="icon" viewBox="0 0 16 16" aria-hidden="true"><circle cx="8" cy="8" r="7"/><path d="M1 8h14M8 1c-3 3-3 11 0 14M8 1c3 3 3 11 0 14" stroke="#474749" stroke-width="1" fill="none"/></svg>
        www.harborsystems.com.au
      </li>
    </ul>
  </div>

  <div class="tagline-band">Complete IT Management</div>
</section>

</body>
</html>
```